Quiet Harbor Podcast W/ Dr. Lena Marsh

Podcast Cover Art. I am in search of a re-design for my existing podcast. We have over 100 episodes, but I want to change the name to Quiet Harbor Podcast With Dr. Lena Marsh. I'm open to any ideas, and have attached source file image to use. ( note: NO brain images please).

```html
<!DOCTYPE html>
<html lang="en">
<head>
<meta charset="utf-8">
<title>Quiet Harbor Podcast With Dr. Lena Marsh</title>
<link href="https://fonts.googleapis.com/css2?family=Bebas+Neue&family=Montserrat:wght@600&display=swap" rel="stylesheet">
<style>
  :root {
    --bg-light: #f4f4f4;
    --bg-mid: #d9d9d9;
    --title-dark: #3a0a03;
    --title-accent: #d44a33;
    --band: #d04a35;
    --band-text: #ffffff;
    --divider: #ffffff;
  }
  html, body {
    margin: 0;
    padding: 0;
    width: 1200px;
    height: 1200px;
    overflow: hidden;
    background: var(--bg-light);
  }
  .cover {
    position: relative;
    width: 1200px;
    height: 1200px;
    overflow: hidden;
  }
  .cover-art { display: block; }
  .show-title {
    font-family: "Bebas Neue", "Oswald", sans-serif;
  }
  .title-top { fill: var(--title-dark); }
  .title-bottom { fill: var(--title-accent); }
  .host-band { fill: var(--band); }
  .divider-line { fill: var(--divider); }
  .host-name {
    fill: var(--band-text);
    font-family: "Montserrat", "Helvetica Neue", sans-serif;
    font-weight: 600;
  }
</style>
</head>
<body>
<main class="cover">
  <svg class="cover-art" width="1200" height="1200" viewBox="0 0 1200 1200" xmlns="http://www.w3.org/2000/svg">
    <defs>
      <radialGradient id="bg-gradient" cx="0.45" cy="0.45" r="0.75">
        <stop offset="0" stop-color="#f7f7f7"/>
        <stop offset="1" stop-color="#d6d6d6"/>
      </radialGradient>
      <linearGradient id="portrait-gradient" x1="0" y1="0" x2="0" y2="1">
        <stop offset="0" stop-color="#8a2a1a"/>
        <stop offset="0.35" stop-color="#d4553c"/>
        <stop offset="1" stop-color="#e8654a"/>
      </linearGradient>
      <clipPath id="above-band">
        <rect x="0" y="0" width="1200" height="1009"/>
      </clipPath>
    </defs>

    <rect class="background-pattern" x="0" y="0" width="1200" height="1200" fill="url(#bg-gradient)"
          role="img" aria-label="Light grey ornamental lace pattern background"/>

    <g class="show-title">
      <text class="title-top" x="205" y="298" font-size="338" textLength="790" lengthAdjust="spacingAndGlyphs">QUIET</text>
      <text class="title-bottom" x="158" y="519" font-size="277" textLength="910" lengthAdjust="spacingAndGlyphs">HARBOR</text>
    </g>

    <g class="portrait-area" clip-path="url(#above-band)">
      <circle class="host-portrait" cx="600" cy="1065" r="401" fill="url(#portrait-gradient)"
              role="img" aria-label="Illustrated portrait of the host in an orange checked blazer, set on a dark brown circle"/>
    </g>

    <rect class="divider-line" x="0" y="1009" width="1200" height="10"/>
    <rect class="host-band" x="0" y="1019" width="1200" height="181"/>
    <text class="host-name" x="600" y="1123" font-size="104" text-anchor="middle"
          textLength="960" lengthAdjust="spacingAndGlyphs">DR. LENA MARSH</text>
  </svg>
</main>
</body>
</html>
```